English and Spanish Language School Needs a Business Card

Need a business card design a startup company called Maribel Language School. The company will offer English and Spanish conversational level courses designed to make the learner feel comfortable with grammar and vocabulary. We would like to see a logo with some colour that should communicate learning, growth.

Target Market(s)

Consumers and businesses

Industry/Entity Type

Education

Contact Information for Business Card

TBD

Font styles to use
Serif

Requirements
Must have
• Include the following
• Logo
• Name
• Title
• Cellphone Number
• Office Phone number
• Email address
• Office Address

```html
<!DOCTYPE html>
<html lang="en">
<head>
<meta charset="utf-8">
<title>Maribel Language School – Business Card</title>
<link rel="stylesheet" href="https://fonts.googleapis.com/css2?family=Tinos:wght@400;700&display=swap">
<style>
  :root{
    --stage:#2b2b2b;
    --brand-red:#c81e26;
    --brand-teal:#1a9ea6;
    --paper:#ffffff;
    --serif:"Tinos","Times New Roman",serif;
  }
  html,body{margin:0;padding:0;overflow:hidden;}
  body{width:1189px;height:1200px;background:var(--stage);position:relative;font-family:var(--serif);}
  .card{position:absolute;left:171px;width:856px;height:487px;box-sizing:border-box;}
  .card--front{top:68px;background:var(--brand-red);}
  .card--back{top:627px;background:var(--paper);}

  .wordmark{position:absolute;font-weight:700;line-height:1;margin:0;}
  .wordmark__name{display:block;letter-spacing:-1px;}
  .wordmark__tag{display:block;}

  .card--front .wordmark{color:var(--paper);left:0;right:0;top:168px;text-align:center;}
  .card--front .wordmark__name{font-size:120px;}
  .card--front .wordmark__tag{font-size:30px;margin-top:6px;}

  .card--back .wordmark{color:var(--brand-red);left:41px;top:50px;}
  .card--back .wordmark__name{font-size:124px;}
  .card--back .wordmark__tag{font-size:30px;margin-top:6px;padding-left:4px;}

  .divider{position:absolute;left:41px;top:299px;width:670px;height:2px;background:var(--brand-teal);}
  .person{position:absolute;right:44px;top:268px;text-align:right;line-height:1;}
  .person__name{color:var(--brand-red);font-weight:700;font-size:28px;display:block;}
  .person__title{color:var(--brand-teal);font-size:22px;display:block;margin-top:2px;}

  .contacts{position:absolute;left:41px;top:364px;margin:0;padding:0;list-style:none;}
  .contacts li{display:flex;align-items:center;height:29px;color:var(--brand-teal);font-size:23px;}
  .contacts svg{width:23px;height:23px;margin-right:5px;flex:none;}

  .address{position:absolute;right:44px;top:392px;text-align:right;color:var(--brand-teal);font-size:23px;line-height:30px;font-style:normal;}
</style>
</head>
<body>
  <section class="card card--front">
    <h1 class="wordmark"><span class="wordmark__name">Maribel</span><span class="wordmark__tag">Language School</span></h1>
  </section>

  <section class="card card--back">
    <h2 class="wordmark"><span class="wordmark__name">Maribel</span><span class="wordmark__tag">Language School</span></h2>

    <div class="divider"></div>
    <div class="person">
      <span class="person__name">DANIEL REYES</span>
      <span class="person__title">Maneger</span>
    </div>

    <ul class="contacts">
      <li>
        <svg viewBox="0 0 24 24" aria-hidden="true"><rect width="24" height="24" fill="#c81e26"/><rect x="8" y="3" width="8" height="18" rx="1" fill="none" stroke="#fff" stroke-width="1.6"/><rect x="9.5" y="5" width="5" height="4" fill="#fff"/></svg>
        123 456 7890
      </li>
      <li>
        <svg viewBox="0 0 24 24" aria-hidden="true"><rect width="24" height="24" fill="#c81e26"/><path d="M4 10c0-3 16-3 16 0v2h-4v-2H8v2H4z" fill="#fff"/><rect x="6" y="13" width="12" height="7" rx="1" fill="#fff"/></svg>
        123 456 7890
      </li>
      <li>
        <svg viewBox="0 0 24 24" aria-hidden="true"><rect width="24" height="24" fill="#c81e26"/><rect x="4" y="7" width="16" height="11" fill="none" stroke="#fff" stroke-width="1.6"/><path d="M4 7l8 6 8-6M4 18l6-5M20 18l-6-5" fill="none" stroke="#fff" stroke-width="1.4"/></svg>
        hello@maribelschool.com
      </li>
    </ul>

    <address class="address">Your Address,2nd Ste<br>Alder Vale, Texas 1234</address>
  </section>
</body>
</html>
```